Harborline Auto LLC

Car Dealer Customer Service
Address: 2874 Cresthaven Road, Shelbyville, TN 37162
web: www.harborlineautoxq.net
email: harborlineautoxq@mailnest.example
Phone: (931) 555-0148
Phone: (629) 555-0173

```html
<!DOCTYPE html>
<html lang="en">
<head>
<meta charset="utf-8">
<title>Harborline Auto LLC – Business Card</title>
<link rel="stylesheet" href="https://fonts.googleapis.com/css2?family=Montserrat:wght@700;800&family=Lato:ital,wght@1,700&family=Roboto:wght@400&display=swap">
<style>
  :root {
    --page-bg: #e4e5e6;
    --brand-blue: #2089c6;
    --brand-blue-deep: #1a74aa;
    --brand-orange: #eaaa3a;
    --ink: #1f1f1f;
    --white: #ffffff;
  }
  * { box-sizing: border-box; margin: 0; padding: 0; }
  html, body { width: 1200px; height: 900px; overflow: hidden; }
  body { background: var(--page-bg); position: relative; }

  .card {
    position: absolute;
    top: 216px;
    width: 309px;
    height: 501px;
    box-shadow: 0 2px 6px rgba(0,0,0,0.18);
  }
  .card--front {
    left: 279px;
    border-radius: 0 62px 0 62px;
    background: linear-gradient(160deg, var(--brand-blue) 0%, var(--brand-blue-deep) 55%, var(--brand-blue) 100%);
    color: var(--white);
    text-align: center;
  }
  .card--back {
    left: 617px;
    border-radius: 62px 0 62px 0;
    background: var(--white);
  }

  .brand-mark {
    position: absolute;
    left: 50%;
    transform: translateX(-50%);
    width: 72px; height: 72px;
    border-radius: 50%;
  }
  .card--front .brand-mark { top: 148px; background: var(--white); }
  .card--back .brand-mark { top: 76px; background: var(--brand-orange); }

  .brand-name {
    position: absolute;
    left: 0; right: 0;
    font-family: "Montserrat", sans-serif;
    font-weight: 800;
    font-size: 23px;
    letter-spacing: 0.3px;
    text-align: center;
    white-space: nowrap;
  }
  .card--front .brand-name { top: 229px; color: var(--white); }
  .card--back .brand-name { top: 175px; color: var(--brand-blue-deep); }

  .tagline {
    position: absolute;
    left: 0; right: 0;
    top: 376px;
    font-family: "Lato", sans-serif;
    font-style: italic;
    font-weight: 700;
    font-size: 28px;
    line-height: 33px;
  }

  .contact {
    position: absolute;
    left: 31px;
    top: 276px;
    font-family: "Roboto", sans-serif;
    color: var(--ink);
    font-size: 14px;
  }
  .contact__name {
    font-family: "Montserrat", sans-serif;
    font-weight: 800;
    font-size: 18px;
    color: var(--brand-blue-deep);
    line-height: 20px;
  }
  .contact__role { color: var(--brand-orange); font-size: 14px; line-height: 16px; }
  .contact__address { margin-top: 17px; line-height: 18px; }
  .contact__list { list-style: none; margin-top: 18px; }
  .contact__list li {
    display: flex; align-items: center; gap: 5px;
    line-height: 18px; white-space: nowrap;
  }
  .contact__list svg { width: 13px; height: 13px; flex: none; fill: var(--brand-blue-deep); }
  .contact__web-domain { color: var(--brand-blue); }
  .contact__email { font-size: 13px; }
</style>
</head>
<body>

<section class="card card--front" aria-label="Card front">
  <span class="brand-mark"></span>
  <p class="brand-name">HARBORLINE AUTO</p>
  <p class="tagline">CAR DEALER<br>CUSTOMER SERVICE</p>
</section>

<section class="card card--back" aria-label="Card back">
  <span class="brand-mark"></span>
  <p class="brand-name">HARBORLINE AUTO</p>

  <div class="contact">
    <p class="contact__name">MARCUS DELANEY</p>
    <p class="contact__role">Managing Director</p>
    <p class="contact__address">2874 Cresthaven Road<br>Shelbyville, TN 37162</p>
    <ul class="contact__list">
      <li>
        <svg viewBox="0 0 24 24" aria-hidden="true"><path d="M6.6 10.8a15 15 0 0 0 6.6 6.6l2.2-2.2a1 1 0 0 1 1-.25 11.4 11.4 0 0 0 3.6.57 1 1 0 0 1 1 1V20a1 1 0 0 1-1 1A17 17 0 0 1 3 4a1 1 0 0 1 1-1h3.5a1 1 0 0 1 1 1c0 1.25.2 2.45.57 3.6a1 1 0 0 1-.25 1z"/></svg>
        (931) 555-0148
      </li>
      <li>
        <svg viewBox="0 0 24 24" aria-hidden="true"><path d="M6.6 10.8a15 15 0 0 0 6.6 6.6l2.2-2.2a1 1 0 0 1 1-.25 11.4 11.4 0 0 0 3.6.57 1 1 0 0 1 1 1V20a1 1 0 0 1-1 1A17 17 0 0 1 3 4a1 1 0 0 1 1-1h3.5a1 1 0 0 1 1 1c0 1.25.2 2.45.57 3.6a1 1 0 0 1-.25 1z"/></svg>
        (629) 555-0173
      </li>
      <li>
        <svg viewBox="0 0 24 24" aria-hidden="true"><path d="M12 2a10 10 0 1 0 0 20 10 10 0 0 0 0-20zm6.9 6h-2.9a15.6 15.6 0 0 0-1.4-3.6A8 8 0 0 1 18.9 8zM12 4a14 14 0 0 1 1.9 4h-3.8A14 14 0 0 1 12 4zM4.3 14a8 8 0 0 1 0-4h3.4a16.5 16.5 0 0 0 0 4zm.8 2h2.9a15.6 15.6 0 0 0 1.4 3.6A8 8 0 0 1 5.1 16zM8 8H5.1a8 8 0 0 1 4.3-3.6A15.6 15.6 0 0 0 8 8zm4 12a14 14 0 0 1-1.9-4h3.8A14 14 0 0 1 12 20zm2.3-6H9.7a14.7 14.7 0 0 1 0-4h4.6a14.7 14.7 0 0 1 0 4zm.3 5.6a15.6 15.6 0 0 0 1.4-3.6h2.9a8 8 0 0 1-4.3 3.6zm1.7-5.6a16.5 16.5 0 0 0 0-4h3.4a8 8 0 0 1 0 4z"/></svg>
        <span>www.<span class="contact__web-domain">harborlineautoxq</span>.net</span>
      </li>
      <li class="contact__email">
        <svg viewBox="0 0 24 24" aria-hidden="true"><path d="M2 5h20v14H2zm2 2v.4l8 5.3 8-5.3V7zm0 2.8V17h16V9.8l-8 5.3z"/></svg>
        harborlineautoxq@mailnest.example
      </li>
    </ul>
  </div>
</section>

</body>
</html>
```